Flyer-Design für persönlichen Lauftrainer
Zielgruppe
Die Trabwerk GmbH entwickelt und vertreibt den persönlichen Lauftrainer KOBAL. KOBAL ist ein elektrisch angetriebenes, automatisch gesteuertes Fahrzeug, mithilfe dessen eine Person ein professionell geplantes Lauftraining im Freien absolvieren kann. Das Gerät übernimmt die Trainingssteuerung und fungiert dabei quasi als ein persönlicher Lauftrainer.
Wir sprechen zwei Kundengruppen an:
1. Privatkunden
2. Institutionelle Kunden wie Physiotherapiezentren und -praxen, Sport- und Wellnesshotels, betriebliches Gesundheitsmanagement und Verleihgeschäfte.
Die Gestaltung, Funktionalität und Ausstattung des Geräts spricht jedoch grundsätzlich die Gesamtheit der Läufer und Fun- und Aktivsportler an.
Aufgabenstellung
Für unseren Produktflyer der DINA 4 und beidseitig bedruckt sein soll, suchen wir nach einem sportlichen, kräftigen, dynamischen Design. Das Design sollte für uns im Nachhinein leicht veränderbar sein (Texte, Bilder, etc.), da wir den Flyer für verschiedene geographische Regionen anpassen werden. Hierfür würden wir z.B. Indesign nutzen. Die Texte, die wir Ihnen mitliefern sollten möglichst so übernommen werden. Wenn Sie die Möglichkeit sehen, den Inhalt in anderer Form darzustellen, dann ist das in Ordnung.
Der Text für den Flyer ist folgender:
Slogan zum großen Bild: Sie brauchen einen persönlichen Lauftrainer?
Zu den kleinen Bildern: Schalten Sie KOBAL ein, wählen Sie ihr Trainingsprogramm und es kann los gehen!
Call to Action: Besuchen Sie www.trabwerk-beispiel.com
Adresse:
Trabwerk GmbH
www.trabwerk-beispiel.com
Text für Flyer:
Ihr Problem
⁃ Sie haben einen vollen Arbeitstag und wollen trotzdem endlich Ihre Fitness verbessern?
⁃ Sie möchten dringend an Ihrer Figur und Ihrem Gewicht arbeiten?
⁃ Sie wollen schon lange an Ihrem ersten 10 Kilometerlauf teilnehmen und sich optimal darauf vorbereiten?
⁃ Sie möchten einen Trainer haben, der Ihnen jederzeit zur Verfügung steht?
⁃ Mit Ihrer Pulsuhr und Ihrer Lauf-App machen Sie nur geringe oder gar keine Trainingsfortschritte?
Unsere Lösung KOBAL Ihr persönlicher Lauftrainer
⁃ bietet Ihnen ein optimales Lauftraining im Freien durch eine kontrollierte, direkte Geschwindigkeitsvorgabe,
⁃ alarmiert Sie nicht nur wenn Sie etwas falsch machen (indirektes Feedback), er zeigt Ihnen wie Sie es richtig machen (direktes Feedback),
⁃ führt dabei Trainingsprogramme aus, die auf Ihre individuellen Fitness- und Leistungsziele zugeschnitten sind,
⁃ verhindert, dass Sie sich beim Training überlasten,
⁃ unterstützt Sie als
⁃ Anfänger beim Trainingseinstieg
⁃ Fortgeschrittene beim Aufba..

```html
<!DOCTYPE html>
<html lang="de">
<head>
<meta charset="utf-8">
<title>Trabwerk – Persönlicher Lauftrainer</title>
<link href="https://fonts.googleapis.com/css2?family=Exo+2:wght@400;600&display=swap" rel="stylesheet">
<style>
  :root {
    --paper: #ffffff;
    --frame-line: #8a8a8a;
    --brand-orange: #e36f22;
    --brand-orange-light: #ec7f2e;
    --brand-orange-dark: #c85a14;
    --sky-top: #dfe6ea;
    --sky-bottom: #f4f3ec;
    --hill-green: #4f5a2c;
    --hill-brown: #7a6a3e;
    --grass-gold: #c89e4c;
    --grass-pale: #d9c596;
    --path-grey: #8e877a;
    --text-on-orange: #ffffff;
  }
  html, body {
    margin: 0;
    padding: 0;
    overflow: hidden;
    background: var(--paper);
  }
  .flyer {
    position: relative;
    width: 1200px;
    height: 848px;
    background: var(--paper);
    box-sizing: border-box;
    border: 1px solid var(--frame-line);
    overflow: hidden;
    font-family: "Exo 2", sans-serif;
  }
  .hero-photo {
    position: absolute;
    left: 20px;
    top: 20px;
    width: 1160px;
    height: 808px;
    background:
      radial-gradient(ellipse 260px 200px at 900px 290px, rgba(255,252,232,0.95) 0%, rgba(255,248,220,0.55) 45%, rgba(255,248,220,0) 100%),
      radial-gradient(ellipse 260px 420px at 520px 820px, rgba(120,112,100,0.85) 0%, rgba(140,130,115,0.5) 55%, rgba(140,130,115,0) 100%),
      radial-gradient(ellipse 330px 190px at 90px 400px, rgba(62,78,34,0.95) 0%, rgba(70,82,38,0.6) 55%, rgba(70,82,38,0) 100%),
      radial-gradient(ellipse 420px 120px at 150px 290px, rgba(74,76,40,0.9) 0%, rgba(74,76,40,0) 100%),
      radial-gradient(ellipse 380px 260px at 1040px 460px, rgba(226,206,150,0.85) 0%, rgba(226,206,150,0) 100%),
      radial-gradient(ellipse 280px 240px at 110px 700px, rgba(206,160,72,0.9) 0%, rgba(206,160,72,0) 100%),
      linear-gradient(180deg,
        var(--sky-top) 0%,
        var(--sky-bottom) 28%,
        #eeeee2 34%,
        var(--hill-brown) 42%,
        #8f7f4c 52%,
        var(--grass-gold) 66%,
        #b39561 82%,
        var(--path-grey) 100%);
  }
  .brand {
    position: absolute;
    left: 832px;
    top: 76px;
    display: flex;
    align-items: center;
    gap: 12px;
  }
  .brand-dot {
    width: 62px;
    height: 62px;
    border-radius: 50%;
    background: var(--brand-orange);
  }
  .brand-name {
    font-size: 54px;
    font-weight: 600;
    line-height: 1;
    color: var(--brand-orange);
  }
  .slogan-box {
    position: absolute;
    left: 628px;
    top: 463px;
    width: 572px;
    height: 184px;
    background: linear-gradient(90deg, var(--brand-orange-dark) 0%, var(--brand-orange) 40%, var(--brand-orange-light) 100%);
    border-radius: 8px 0 0 8px;
  }
  .slogan-box::before {
    content: "";
    position: absolute;
    left: 7px;
    top: 7px;
    right: 0;
    bottom: 7px;
    border: 1px solid rgba(255,255,255,0.85);
    border-right: none;
    border-radius: 6px 0 0 6px;
  }
  .slogan-fold {
    position: absolute;
    left: 1180px;
    top: 647px;
    width: 20px;
    height: 14px;
  }
  .slogan {
    position: absolute;
    left: 35px;
    top: 36px;
    margin: 0;
    font-size: 43px;
    font-weight: 400;
    line-height: 52px;
    color: var(--text-on-orange);
    white-space: nowrap;
  }
</style>
</head>
<body>
  <main class="flyer">
    <div class="hero-photo" role="img" aria-label="Foto: Ein Läufer in grauem Kapuzenpullover stützt sich erschöpft auf die Knie, auf einem Feldweg zwischen goldenem Gras und grünen Hügeln im Gegenlicht der Sonne"></div>

    <div class="brand">
      <span class="brand-dot" aria-hidden="true"></span>
      <span class="brand-name">trabwerk</span>
    </div>

    <section class="slogan-box">
      <h1 class="slogan">Sie brauchen einen<br>persönlichen Lauftrainer?</h1>
    </section>
    <svg class="slogan-fold" viewBox="0 0 20 14" aria-hidden="true">
      <polygon points="0,0 20,0 0,14" fill="#9d4510"/>
    </svg>
  </main>
</body>
</html>
```